Business card for Luxury Portable Restroom Trailer company

We are a Luxury Portable Restroom Trailer Company Called FALCRIDGE HIRES. Based in Orange County California. We provide portable restroom trailers for events, such as, Weddings, Concerts, Charity events, Sporting events, Tournaments, Corporate events, ect. We rent and Sell the Luxury restrooms. Our colors are white, grey, and Orange. As you will see in the logo we uploaded.
There are 2 people in the company so the names and titles will change for the 3 people but card will remain the same. Here is the information for each Person: Dwight Penner CFO 555 318-0476
next Person: Leon Marchetti VP 555 318-0476
Next Person: Owen Marchetti CEO 555 318-0476
Information to include on the card: Luxury Restroom Trailers Rental and Sales. Weddings, Concerts, Charity, Sporting and Corp. Events.

```html
<!DOCTYPE html>
<html lang="en">
<head>
<meta charset="utf-8">
<title>Falcridge Hires – Business Card</title>
<link href="https://fonts.googleapis.com/css2?family=Michroma&display=swap" rel="stylesheet">
<style>
  :root {
    --bg: #6b6d70;
    --card-white: #ffffff;
    --card-dark: #4a4b4d;
    --ink: #4d4d4f;
    --orange: #f26522;
    --line-dark: #2f3032;
  }
  * { margin: 0; padding: 0; box-sizing: border-box; }
  html, body { width: 1200px; height: 876px; overflow: hidden; }
  body {
    background: var(--bg);
    font-family: "Michroma", sans-serif;
    display: flex;
    align-items: center;
    justify-content: center;
    gap: 40px;
  }
  .card {
    width: 540px;
    height: 309px;
    position: relative;
    border-radius: 2px;
    box-shadow: 0 10px 28px rgba(0,0,0,0.35);
  }
  .card--front { background: var(--card-white); color: var(--ink); }
  .card--back {
    background: var(--card-dark);
    display: flex;
    align-items: center;
    justify-content: center;
  }

  .brand {
    position: absolute;
    left: 30px;
    top: 34px;
    display: flex;
    align-items: center;
    gap: 10px;
  }
  .brand__mark {
    width: 14px;
    height: 14px;
    background: var(--ink);
  }
  .brand__name {
    font-size: 15px;
    letter-spacing: 1px;
    color: var(--ink);
  }

  .person {
    position: absolute;
    left: 230px;
    top: 104px;
  }
  .person__name {
    font-size: 17px;
    letter-spacing: 1px;
    text-transform: uppercase;
    color: var(--ink);
    white-space: nowrap;
  }
  .person__name .first { color: var(--orange); }
  .person__title {
    font-size: 11px;
    margin-top: 6px;
    letter-spacing: 1px;
  }
  .person__phone {
    display: flex;
    align-items: center;
    gap: 6px;
    margin-top: 6px;
    font-size: 12px;
    letter-spacing: 1px;
  }
  .person__phone svg { width: 12px; height: 12px; }

  .services {
    position: absolute;
    left: 30px;
    bottom: 40px;
  }
  .services__headline {
    font-size: 11px;
    color: var(--orange);
    text-transform: uppercase;
    letter-spacing: 0.5px;
  }
  .services__list {
    font-size: 9.5px;
    margin-top: 8px;
    letter-spacing: 0.3px;
  }
  .services__list .sep { color: var(--orange); padding: 0 3px; }

  .back-brand {
    width: 180px;
    height: 180px;
    border: 3px solid var(--line-dark);
    border-radius: 50%;
    display: flex;
    align-items: center;
    justify-content: center;
    text-align: center;
    font-size: 14px;
    line-height: 1.6;
    letter-spacing: 1px;
    color: var(--line-dark);
  }
</style>
</head>
<body>
  <section class="card card--front">
    <div class="brand">
      <span class="brand__mark"></span>
      <span class="brand__name">FALCRIDGE HIRES</span>
    </div>

    <div class="person">
      <div class="person__name"><span class="first">Leon</span> Marchetti</div>
      <div class="person__title">CFO</div>
      <div class="person__phone">
        <svg viewBox="0 0 24 24" aria-hidden="true">
          <path fill="#f26522" d="M6.6 10.8a15.1 15.1 0 0 0 6.6 6.6l2.2-2.2a1 1 0 0 1 1-.25 11.4 11.4 0 0 0 3.6.57 1 1 0 0 1 1 1V20a1 1 0 0 1-1 1A17 17 0 0 1 3 4a1 1 0 0 1 1-1h3.5a1 1 0 0 1 1 1c0 1.25.2 2.45.57 3.57a1 1 0 0 1-.25 1z"/>
        </svg>
        <span>555.318.0476</span>
      </div>
    </div>

    <div class="services">
      <div class="services__headline">Luxury Restroom Trailers Rental and Sales</div>
      <div class="services__list">Weddings<span class="sep">|</span>Concerts<span class="sep">|</span>Charity<span class="sep">|</span>Sporting<span class="sep">|</span>Corp. Events</div>
    </div>
  </section>

  <section class="card card--back">
    <div class="back-brand">FALCRIDGE<br>HIRES</div>
  </section>
</body>
</html>
```